Home Page Design (+50 More Pages To Winning Designer!)

We have a 50+ page website, but we're starting with the home page. The winning designer will get all 50+ pages to design as a 2nd project, so make sure you do your best!

Velorane is in the private jet industry and needs a re-designed website.

We have created the structure for the website and content inside of Frandle.io (THESE ARE ONLY ROUGH A.I. GENERATED WIREFRAMES AND DO NOT NEED TO BE FOLLOWED EXACTLY) - https://www.frandle.io/app/project/K482915_qWmRtZaLs-KDnHoUvvy82QJ5cfhaR61trkwqlDV3Hm

Take the content from the 'Home Page' under the 'Wireframe' tab on the Frandle.io link above, but feel free to re-design the page in a better way as these are only A.I. generated wireframes.

We want a DARK theme.... High quality, luxurious feel, greyscale colors. Attached is a brand guideline (BUT THIS IS NOT A 100% BRAND GUIDELINE, YOU CAN CHANGE COLORS AND FONTS AND MAKE CHANGES IF YOU HAVE BETTER IDEAS) and attached is our logo. We are also attaching some examples of other apps and websites to give you a guideline of what we're looking for for this design project.

The final design MUST communicate luxury using high-quality imagery of large cabin luxurious private jets.
Updates

ENTRIES THAT DO NOT FOLLOW THE PROJECT BRIEF WILL BE AUTOMATICALLY DISCARDED. FOLLOW THE INSTRUCTIONS!

Industry/Entity Type

Travel

Number of Pages Required

1 page

Font styles to use
Sans Serif

Colors

Designer to choose colors to be used in the design.

Requirements
Must have
• Follow wireframe and use content in wireframe (see Frandle.io link)

```html
<!DOCTYPE html>
<html lang="en">
<head>
<meta charset="utf-8">
<title>Velorane — Home</title>
<link rel="stylesheet" href="https://fonts.googleapis.com/css2?family=Inter:wght@400;500;600;700&display=swap">
<style>
:root{
  --page:#353535;
  --nav:#333333;
  --black:#000000;
  --white:#ffffff;
  --card:#5a5a5a;
  --tile:#666666;
  --faq:#5b5b5b;
  --field:#efefef;
  --footer:#2a2a2a;
  --muted:#d0d0d0;
  --line:#5f5f5f;
}
*{box-sizing:border-box;margin:0;padding:0}
html,body{width:1200px;height:3914px;overflow:hidden}
body{background:var(--page);color:var(--white);font-family:"Inter",sans-serif;position:relative}
.abs{position:absolute}
.btn{position:absolute;border:2px solid var(--white);color:var(--white);display:flex;align-items:center;justify-content:center;font-size:20px;font-weight:400;background:transparent}
.h2{position:absolute;font-size:40px;font-weight:700;line-height:1.2}
.lead{position:absolute;font-size:20px;line-height:1.42;color:#f0f0f0}

/* nav */
.nav{left:0;top:0;width:1200px;height:82px;background:var(--nav)}
.nav-cut{left:0;top:0}
.brand{font-weight:400;letter-spacing:-0.5px}
.nav .brand{position:absolute;left:72px;top:20px;font-size:34px}
.menu{position:absolute;left:286px;top:32px;display:flex;gap:34px;font-size:16px}
.menu .active{font-weight:700}
.signup{position:absolute;left:923px;top:32px;font-size:16px;color:#111}
.signin{position:absolute;left:1013px;top:24px;width:115px;height:34px;border:1.5px solid #222;color:#111;font-size:16px;display:flex;align-items:center;justify-content:center}

/* hero (children positioned relative to the hero box) */
.hero{left:0;top:82px;width:1200px;height:667px;overflow:hidden}
.hero-photo{position:absolute;inset:0;background:linear-gradient(90deg,#161616 0%,#262626 35%,#555 62%,#6e6e6e 80%,#3e3e3e 100%)}
.hero-title{left:72px;top:136px;font-size:58px;font-weight:700;line-height:1.12}
.hero-text{left:72px;top:272px;width:540px;font-size:20.5px;line-height:1.4}

/* features */
.feature{position:absolute;width:282px;height:217px;background:linear-gradient(180deg,#8a8a8a 0%,#6f6f6f 55%,#4e4e4e 100%)}
.feature h3{position:absolute;left:26px;top:130px;font-size:20px;font-weight:700}
.feature p{position:absolute;left:26px;top:158px;width:240px;font-size:11px;line-height:1.8;color:#e6e6e6}

/* why */
.tile{position:absolute;width:179px;height:179px;background:var(--tile);display:flex;flex-direction:column;align-items:center;justify-content:flex-end;padding-bottom:32px;text-align:center;font-size:20px;font-weight:700;line-height:1.25}
.tile svg{margin-bottom:18px}

/* offer */
.offer{position:absolute;top:1929px;width:211px;height:296px;background:linear-gradient(180deg,#9a9a9a 0%,#6a6a6a 45%,#2a2a2a 80%,#000 100%)}
.offer span{position:absolute;left:30px;bottom:26px;font-size:20px;font-weight:700;line-height:1.25}

/* consult */
.band{left:0;top:2353px;width:1200px;height:292px;background:var(--black)}
.form-box{left:614px;top:2289px;width:513px;height:419px;background:var(--white);color:#111}
.form-box h3{position:absolute;left:48px;top:40px;font-size:29px;font-weight:600}
.field{position:absolute;left:48px;width:417px;background:var(--field);color:#333;font-size:15px;padding:18px 25px}
.send{position:absolute;left:48px;top:337px;width:135px;height:47px;background:#000;color:#fff;font-size:20px;display:flex;align-items:center;justify-content:center}

/* testimonials */
.review{position:absolute;top:2774px;width:282px;height:203px;background:var(--card);overflow:hidden}
.avatar{position:absolute;left:24px;top:22px;width:56px;height:56px;border-radius:50%;background:radial-gradient(circle at 50% 40%,#777,#2a2a2a)}
.review h4{position:absolute;left:96px;top:28px;font-size:20px;font-weight:600}
.review time{position:absolute;left:96px;top:56px;font-size:10px;color:#ddd}
.review p{position:absolute;left:22px;top:98px;width:238px;font-size:11px;line-height:2;color:#e4e4e4;text-align:justify}

/* logo strip */
.strip{position:absolute;top:3078px;font-size:45px;white-space:nowrap}

/* faq */
.faq{position:absolute;left:538px;width:589px;background:var(--faq);font-size:16px;line-height:1.75;color:#f2f2f2;padding:0 90px 0 32px;display:flex;align-items:center}
.faq svg{position:absolute;right:30px;top:50%;margin-top:-8px}

/* footer */
.footer{left:0;top:3567px;width:1200px;height:347px;background:var(--footer)}
.footer .brand{position:absolute;left:99px;top:80px;font-size:34px}
.f-about{position:absolute;left:99px;top:133px;width:226px;font-size:11.5px;line-height:1.55;text-align:justify;color:#e8e8e8}
.socials{position:absolute;left:99px;top:226px;display:flex;gap:8px}
.socials span{width:27px;height:27px;border-radius:50%;background:var(--white)}
.f-col{position:absolute;font-size:12px;line-height:25px;color:#e8e8e8}
.f-col b{display:block;font-weight:700;color:#fff}
.sub-title{position:absolute;left:790px;top:45px;font-size:16px;font-weight:700}
.sub-input{position:absolute;left:790px;top:74px;width:310px;height:40px;background:#fff;color:#999;font-size:11px;padding:13px 15px}
.sub-btn{position:absolute;left:790px;top:126px;width:128px;height:32px;background:#666;font-size:12px;display:flex;align-items:center;justify-content:center}
.f-rule{position:absolute;left:99px;top:294px;width:1001px;height:1px;background:var(--line)}
.copy{position:absolute;left:0;top:316px;width:1200px;text-align:center;font-size:9px;color:#8a8a8a}
</style>
</head>
<body>

<!-- Navigation -->
<header class="abs nav">
  <svg class="abs nav-cut" width="1200" height="82" aria-hidden="true"><polygon points="782,0 1200,0 1200,82 855,82" fill="#ffffff"/></svg>
  <div class="brand">Velorane</div>
  <nav class="menu"><span class="active">Home</span><span>Features</span><span>Services</span><span>Membership</span><span>About</span></nav>
  <span class="signup">Sign Up</span>
  <span class="signin">Sign In</span>
</header>

<!-- Hero -->
<section class="abs hero">
  <div class="hero-photo" role="img" aria-label="Traveller in a suit walking toward a private jet on a wet tarmac at dusk"></div>
  <svg class="abs" style="left:0;top:0" width="1200" height="667" aria-hidden="true"><polygon points="802,0 1200,0 1200,452" fill="#333333"/></svg>
  <h1 class="abs hero-title">Fly with Us, Crafting<br>Limitless Journeys</h1>
  <p class="abs hero-text">Lorem ipsum dolor sit amet, consectetur adipiscing elit. Sed do eiusmod tempor incididunt ut labore et dolore magna aliqua. Ut enim ad minim veniam, quis nostrud exercitation ullamco laboris nisi ut aliquip ex ea commodo consequat.</p>
  <div class="btn" style="left:73px;top:456px;width:210px;height:47px">Get Started</div>
</section>

<!-- Features -->
<h2 class="h2" style="left:73px;top:811px">Our Features</h2>
<p class="lead" style="left:73px;top:870px;width:410px">Lorem ipsum dolor sit amet, consectetur adipiscing elit. Sed do eiusmod tempor incididunt ut labore.</p>
<div class="btn" style="left:73px;top:996px;width:190px;height:47px">See More</div>

<div class="feature" style="left:538px;top:811px" role="img" aria-label="Private jet parked in a lit hangar"><h3>Private Jet Lease</h3><p>Lorem ipsum dolor sit amet, consectetur adipiscing elit.</p></div>
<div class="feature" style="left:845px;top:811px" role="img" aria-label="Airliner on a runway under a grey sky"><h3>All Access</h3><p>Lorem ipsum dolor sit amet, consectetur adipiscing elit.</p></div>
<div class="feature" style="left:538px;top:1054px" role="img" aria-label="Helicopter flying against clouds"><h3>Helicopter Access</h3><p>Lorem ipsum dolor sit amet, consectetur adipiscing elit.</p></div>
<div class="feature" style="left:845px;top:1054px" role="img" aria-label="Aircraft cabin aisle with rows of seats"><h3>Seat Charter Flights</h3><p>Lorem ipsum dolor sit amet, consectetur adipiscing elit.</p></div>

<!-- Why -->
<h2 class="h2" style="left:73px;top:1334px">Why Velorane?</h2>
<p class="lead" style="left:73px;top:1392px;width:410px">Lorem ipsum dolor sit amet, consectetur adipiscing elit. Sed do eiusmod tempor incididunt ut labore.</p>
<div class="btn" style="left:73px;top:1518px;width:207px;height:47px">Learn More</div>

<div class="tile" style="left:538px;top:1335px">
  <svg width="76" height="48" viewBox="0 0 76 48" fill="none" stroke="#fff" stroke-width="4" stroke-linecap="round" stroke-linejoin="round"><path d="M10 38a14 14 0 0 1 20-24l16 20a14 14 0 0 0 22-18"/><path d="M30 6l2 10-10 1"/><path d="M46 42l-2-10 10-1"/></svg>
  Flexible</div>
<div class="tile" style="left:743px;top:1335px">
  <svg width="56" height="64" viewBox="0 0 56 64" fill="none" stroke="#fff" stroke-width="4" stroke-linecap="round"><path d="M22 4h8a10 10 0 0 1 0 20H22"/><path d="M22 14h14"/><path d="M8 34h34a10 10 0 0 1 0 20H8"/><path d="M16 44h36"/><path d="M22 4v20"/></svg>
  Private</div>
<div class="tile" style="left:948px;top:1335px">
  <svg width="72" height="60" viewBox="0 0 72 60" fill="none" stroke="#fff" stroke-width="4" stroke-linejoin="round"><path d="M30 4h8l4 20h22a6 6 0 0 1 0 12H42l-4 20h-8l2-20H14l-4 8H4l2-14-2-14h6l4 8h18z"/></svg>
  Non-stop</div>
<div class="tile" style="left:538px;top:1539px">
  <svg width="72" height="56" viewBox="0 0 72 56" fill="none" stroke="#fff" stroke-width="4" stroke-linejoin="round" stroke-linecap="round"><path d="M36 30c-10-6-14-12-14-18a8 8 0 0 1 14-4 8 8 0 0 1 14 4c0 6-4 12-14 18z"/><path d="M4 34h14l12 8h12a4 4 0 0 1 0 8H26"/><path d="M4 52h30l30-14a5 5 0 0 0-6-8l-16 8"/></svg>
  Special<br>Services</div>
<div class="tile" style="left:743px;top:1539px">
  <svg width="60" height="66" viewBox="0 0 60 66" fill="none" stroke="#fff" stroke-width="4" stroke-linejoin="round" stroke-linecap="round"><path d="M30 4l24 8v18c0 16-10 26-24 32C16 56 6 46 6 30V12z"/><path d="M19 33l8 8 15-16"/></svg>
  Secure</div>
<div class="tile" style="left:948px;top:1539px">
  <svg width="64" height="62" viewBox="0 0 64 62" fill="none" stroke="#fff" stroke-width="4" stroke-linejoin="round" stroke-linecap="round"><path d="M8 6l6 6 12-4 6 2-8 6 8 2 4-2 2 2-6 4-16-2-6-6z"/><path d="M44 22h12v8H44z"/><path d="M50 30v26"/><path d="M4 58h56"/></svg>
  Access<br>to the Airport</div>

<!-- Offer -->
<h2 class="h2" style="left:0;top:1781px;width:1200px;text-align:center">What We Offer</h2>
<p class="lead" style="left:290px;top:1838px;width:620px;text-align:center">Lorem ipsum dolor sit amet, consectetur adipiscing elit. Sed do eiusmod tempor incididunt ut labore.</p>

<svg class="abs" style="left:60px;top:2058px" width="26" height="40" viewBox="0 0 26 40" aria-hidden="true"><path d="M20 4L6 20l14 16" fill="none" stroke="#fff" stroke-width="5" stroke-linecap="round" stroke-linejoin="round"/></svg>
<svg class="abs" style="left:1114px;top:2058px" width="26" height="40" viewBox="0 0 26 40" aria-hidden="true"><path d="M6 4l14 16L6 36" fill="none" stroke="#fff" stroke-width="5" stroke-linecap="round" stroke-linejoin="round"/></svg>

<div class="offer" style="left:144px" role="img" aria-label="Leather cabin seats"><span>On-demand<br>Charter</span></div>
<div class="offer" style="left:378px" role="img" aria-label="Technicians servicing an aircraft in a hangar"><span>Plane<br>Management</span></div>
<div class="offer" style="left:611px" role="img" aria-label="Nose of a jet seen from below"><span>Private Jet<br>Membership</span></div>
<div class="offer" style="left:845px" role="img" aria-label="Cabin crew member in the aisle"><span>Cabin and<br>Crew Services</span></div>

<!-- Consultation -->
<section class="abs band"></section>
<h2 class="h2" style="left:73px;top:2397px">Need Consultation?</h2>
<p class="lead" style="left:73px;top:2455px;width:460px">If you need a personalize consultation or want to be our member, please contact us in here.</p>
<div class="btn" style="left:73px;top:2553px;width:207px;height:47px">Contact Us</div>

<form class="abs form-box">
  <h3>For the Further Information</h3>
  <div class="field" style="top:91px;height:52px">Write your name</div>
  <div class="field" style="top:158px;height:52px">Write your email</div>
  <div class="field" style="top:225px;height:97px">Write your message</div>
  <div class="send">Send</div>
</form>

<!-- Testimonials -->
<h2 class="h2" style="left:73px;top:2771px">What People Say?</h2>
<p class="lead" style="left:73px;top:2830px;width:410px">Lorem ipsum dolor sit amet, consectetur adipiscing elit. Sed do eiusmod tempor.</p>
<div class="btn" style="left:73px;top:2929px;width:190px;height:47px">See More</div>

<article class="review" style="left:538px"><div class="avatar" role="img" aria-label="Reviewer portrait"></div><h4>Marcus Hale</h4><time>January, 24 2024</time><p>Lorem ipsum dolor sit amet, consectetur adipiscing elit. Sed do eiusmod tempor incididunt ut labore et dolore magna aliqua. Ut enim ad minim veniam.</p></article>
<article class="review" style="left:845px"><div class="avatar" role="img" aria-label="Reviewer portrait"></div><h4>Marcus Hale</h4><time>January, 24 2024</time><p>Lorem ipsum dolor sit amet, consectetur adipiscing elit. Sed do eiusmod tempor incididunt ut labore et dolore magna aliqua. Ut enim ad minim veniam.</p></article>
<article class="review" style="left:1153px"><div class="avatar" role="img" aria-label="Reviewer portrait"></div><h4>Marcus Hale</h4><time>January, 24 2024</time><p>Lorem ipsum dolor sit amet, consectetur adipiscing elit. Sed do eiusmod tempor incididunt ut labore et dolore magna aliqua.</p></article>

<!-- Brand strip -->
<div class="strip brand" style="left:-128px">Velorane</div>
<div class="strip brand" style="left:126px">Velorane</div>
<div class="strip brand" style="left:381px">Velorane</div>
<div class="strip brand" style="left:636px">Velorane</div>
<div class="strip brand" style="left:892px">Velorane</div>
<div class="strip brand" style="left:1147px">Velorane</div>

<!-- FAQ -->
<h2 class="h2" style="left:73px;top:3287px;line-height:1.22">Frequently Ask<br>Question</h2>
<p class="lead" style="left:73px;top:3392px;width:410px">Lorem ipsum dolor sit amet, consectetur adipiscing elit. Sed do eiusmod tempor.</p>

<div class="faq" style="top:3205px;height:91px">How much does it cost to rent a plane for a one-time flight or a monthly/annual subscription?<svg width="22" height="16" viewBox="0 0 22 16"><path d="M3 4l8 8 8-8" fill="none" stroke="#fff" stroke-width="3"/></svg></div>
<div class="faq" style="top:3309px;height:91px">What types of aircraft are available for charter and what are their capacities?<svg width="22" height="16" viewBox="0 0 22 16"><path d="M3 4l8 8 8-8" fill="none" stroke="#fff" stroke-width="3"/></svg></div>
<div class="faq" style="top:3415px;height:91px">Do you provide additional services such as custom meals, cabin service, or ground transportation?<svg width="22" height="16" viewBox="0 0 22 16"><path d="M3 4l8 8 8-8" fill="none" stroke="#fff" stroke-width="3"/></svg></div>

<!-- Footer -->
<footer class="abs footer">
  <div class="brand">Velorane</div>
  <p class="f-about">Lorem ipsum dolor sit amet, consectetur adipiscing elit. Sed do eiusmod tempor incididunt ut labore et dolore magna aliqua.</p>
  <div class="socials"><span></span><span></span><span></span></div>
  <div class="f-col" style="left:400px;top:38px"><b>Contact Us</b>support@velorane.com<br>Tel. 123 456 7890<br><b style="margin-top:8px">Company</b>Contact Us<br>FAQ</div>
  <div class="f-col" style="left:640px;top:38px"><b>Quick Links</b>Features<br>Services<br>Membership<br>About Us<br>Support<br>Testimonial</div>
  <div class="sub-title">Subscribe for More Updates</div>
  <div class="sub-input">Write your email</div>
  <div class="sub-btn">Subscribe</div>
  <div class="f-rule"></div>
  <div class="copy">© 2024 Velorane | Privacy Policy | Term &amp; Conditions</div>
</footer>

</body>
</html>
```